Local Flower Farm Needs Business Card Design

I need business cards designed for a flower farm based in Eudora, Kansas.
Business Info:
We are a local cut flower farm located in Eudora, Kansas, founded by Corinne Haldwick. What started as a passion for agriculture and search for more joy in daily life has blossomed into a small business dedicated to providing the community with beautiful, fresh, and sustainable flowers. We specialize in local, seasonal blooms, ensuring that every petal reflects the care and dedication we pour into our craft. Our mission is to deliver the highest quality flowers directly to our customers through local farmers markets and to florists who share our commitment to sustainability. Join us in celebrating the beauty of nature, one bloom at a time!
Contact Details:
Corinne Haldwick
Owner
Phone 913-555-0147
Facebook: Rosalind Thorpe Gardens
Instagram: @RosalindThorpeGardens
Website: RosalindThorpeGardens.example
Target Market(s)
Wholesale to Florists and Direct to Consumer via Farmers Market
Industry/Entity Type
Florist, Farm
Contact Information for Business Card
Name, Contact Info, Logo
Look and feel
Each slider illustrates characteristics of the customer's brand and the style your logo design should communicate.

```html
<!DOCTYPE html>
<html lang="en">
<head>
<meta charset="utf-8">
<title>Rosalind Thorpe Gardens — Business Card</title>
<link rel="stylesheet" href="https://fonts.googleapis.com/css2?family=EB+Garamond:wght@400;600&display=swap">
<style>
  :root {
    --backdrop: #cbcccc;
    --card: #ffffff;
    --forest: #173a36;
    --mist: #b7b9b9;
    --ink: #111a19;
  }
  * { box-sizing: border-box; margin: 0; padding: 0; }
  html, body { width: 1200px; height: 813px; overflow: hidden; }
  body {
    background: var(--backdrop);
    font-family: "EB Garamond", Georgia, serif;
    color: var(--ink);
    position: relative;
  }
  .card {
    position: absolute;
    width: 520px;
    height: 297px;
    top: 258px;
    background: var(--card);
    border-radius: 22px;
    overflow: hidden;
    box-shadow: 0 10px 24px rgba(0,0,0,0.22);
  }
  .card--front { left: 55px; }
  .card--back { left: 625px; }

  .brand-seal {
    position: absolute;
    border: 2px solid var(--forest);
    border-radius: 50%;
    display: flex;
    align-items: center;
    justify-content: center;
    text-align: center;
    color: var(--forest);
    font-weight: 400;
    letter-spacing: 0.08em;
    text-transform: uppercase;
    line-height: 1.25;
  }
  .card--front .brand-seal {
    width: 190px; height: 190px;
    left: 165px; top: 53px;
    font-size: 21px;
  }
  .card--back .brand-seal {
    width: 150px; height: 150px;
    left: 322px; top: 62px;
    font-size: 16px;
  }

  .back-bands { position: absolute; inset: 0; width: 100%; height: 100%; }

  .contact {
    position: absolute;
    left: 26px;
    top: 116px;
  }
  .contact__name { font-size: 17px; font-weight: 600; line-height: 1.1; }
  .contact__role { font-size: 11px; margin: 3px 0 7px; }
  .contact__list { list-style: none; }
  .contact__item {
    display: flex;
    align-items: center;
    gap: 5px;
    font-size: 13px;
    line-height: 1.35;
  }
  .contact__icon { width: 10px; height: 10px; flex: none; }
</style>
</head>
<body>

  <section class="card card--front" aria-label="Card front">
    <div class="brand-seal">Rosalind<br>Thorpe<br>Gardens</div>
  </section>

  <section class="card card--back" aria-label="Card back">
    <svg class="back-bands" viewBox="0 0 520 297" preserveAspectRatio="none" aria-hidden="true">
      <path d="M0 0 H520 V62 C420 30 300 22 160 34 C90 40 40 30 0 22 Z" fill="var(--forest)"/>
      <path d="M0 22 C40 30 90 40 160 34 C300 22 420 30 520 62 V74 C420 42 300 34 160 46 C90 52 40 42 0 34 Z" fill="var(--mist)"/>
      <path d="M0 297 H520 V206 C470 256 380 274 250 276 C150 278 60 274 0 268 Z" fill="var(--forest)"/>
      <path d="M0 268 C60 274 150 278 250 276 C380 274 470 256 520 206 V192 C470 244 380 262 250 264 C150 266 60 262 0 256 Z" fill="var(--mist)"/>
    </svg>

    <div class="brand-seal">Rosalind<br>Thorpe<br>Gardens</div>

    <div class="contact">
      <p class="contact__name">Corinne Haldwick</p>
      <p class="contact__role">Owner</p>
      <ul class="contact__list">
        <li class="contact__item">
          <svg class="contact__icon" viewBox="0 0 10 10" aria-hidden="true"><path d="M2 1 L4 1 L4.6 3 L3.4 4 C4 5.3 4.8 6.1 6 6.6 L7 5.4 L9 6 L9 8 C9 8.6 8.6 9 8 9 C4.2 8.8 1.2 5.8 1 2 C1 1.4 1.4 1 2 1 Z" fill="var(--ink)"/></svg>
          913-555-0147
        </li>
        <li class="contact__item">
          <svg class="contact__icon" viewBox="0 0 10 10" aria-hidden="true"><circle cx="5" cy="5" r="4.2" fill="none" stroke="var(--ink)" stroke-width="1"/><ellipse cx="5" cy="5" rx="1.8" ry="4.2" fill="none" stroke="var(--ink)" stroke-width="0.8"/><line x1="0.8" y1="5" x2="9.2" y2="5" stroke="var(--ink)" stroke-width="0.8"/></svg>
          RosalindThorpeGardens.example
        </li>
        <li class="contact__item">
          <svg class="contact__icon" viewBox="0 0 10 10" aria-hidden="true"><rect x="1" y="1" width="8" height="8" rx="1.5" fill="var(--ink)"/></svg>
          Rosalind Thorpe Gardens
        </li>
        <li class="contact__item">
          <svg class="contact__icon" viewBox="0 0 10 10" aria-hidden="true"><rect x="1" y="1" width="8" height="8" rx="1.5" fill="none" stroke="var(--ink)" stroke-width="1.2"/></svg>
          @RosalindThorpeGardens
        </li>
      </ul>
    </div>
  </section>

</body>
</html>
```